Brightfield Ventures Inc. Letterhead

Creation of attractive and eye catching letterhead for a business start-up for the construction industry. Letterhead must relate to construction, but avoid standard hammer and tools in the design.

I forgot to add some details, sorry about that. Some pertinent info: Ph: 916-555-0187 brightfieldventures.example 448 Willowmere Ave, Ste 210 Folsom, CA 95999 info@brightfieldventures.example not sure if slogan should be in there" “Connecting construction professionals to create a purpose driven industry.” must be able to be used in word. Thanks!

```html
<!DOCTYPE html>
<html lang="en">
<head>
<meta charset="utf-8">
<title>Brightfield Ventures Inc. Letterhead</title>
<link rel="stylesheet" href="https://fonts.googleapis.com/css2?family=Lato:wght@400;700&family=Montserrat:wght@600&family=Kaushan+Script&display=swap">
<style>
  :root {
    --navy: #1c1f5a;
    --red: #c1202a;
    --white: #ffffff;
    --body-text: #474747;
  }
  html, body {
    margin: 0;
    padding: 0;
    overflow: hidden;
    background: var(--white);
  }
  .letterhead {
    position: relative;
    width: 855px;
    height: 1200px;
    background: var(--white);
    overflow: hidden;
    font-family: "Lato", sans-serif;
  }
  .header-shape {
    position: absolute;
    top: 0;
    left: 0;
  }
  .brand {
    position: absolute;
    left: 52px;
    top: 140px;
    display: flex;
    align-items: center;
    gap: 10px;
  }
  .brand-mark {
    width: 14px;
    height: 14px;
    background: var(--red);
  }
  .brand-name {
    font-family: "Montserrat", sans-serif;
    font-weight: 600;
    font-size: 21px;
    letter-spacing: 1.5px;
    color: var(--navy);
    text-transform: uppercase;
  }
  .contact {
    position: absolute;
    right: 63px;
    top: 36px;
    margin: 0;
    padding: 0;
    list-style: none;
    text-align: right;
    color: var(--white);
    font-size: 12.5px;
    line-height: 1;
  }
  .contact li {
    display: flex;
    justify-content: flex-end;
    align-items: center;
    gap: 5px;
  }
  .contact .address { margin-bottom: 17px; }
  .contact .phone { margin-bottom: 6px; }
  .contact .email { margin-bottom: 6px; }
  .contact svg {
    width: 10px;
    height: 10px;
    fill: none;
    stroke: var(--white);
    stroke-width: 1.4;
  }
  .letter {
    position: absolute;
    left: 63px;
    top: 322px;
    width: 730px;
  }
  .salutation {
    margin: 0 0 22px;
    font-weight: 700;
    font-size: 16px;
    color: var(--navy);
  }
  .letter p.body-copy {
    margin: 0 0 19px;
    font-size: 16px;
    line-height: 28px;
    color: var(--body-text);
    text-align: justify;
  }
  .closing {
    margin: 28px 0 0;
    font-size: 19px;
    color: #222;
  }
  .signature {
    margin: 2px 0 0;
    font-family: "Kaushan Script", cursive;
    font-size: 32px;
    color: var(--navy);
  }
  .footer-band {
    position: absolute;
    left: 0;
    bottom: 0;
    width: 855px;
    height: 14px;
    background: var(--red);
  }
</style>
</head>
<body>
<main class="letterhead">
  <svg class="header-shape" width="855" height="320" viewBox="0 0 855 320" aria-hidden="true">
    <rect width="855" height="300" fill="var(--navy)"/>
    <polygon points="0,142 173,2 855,287 855,320 0,320" fill="var(--white)"/>
    <polyline points="0,152 173,14 855,298" fill="none" stroke="var(--red)" stroke-width="5"/>
    <polygon points="0,158 173,20 855,305 855,320 0,320" fill="var(--white)"/>
  </svg>

  <div class="brand">
    <span class="brand-mark"></span>
    <span class="brand-name">Brightfield Ventures</span>
  </div>

  <ul class="contact">
    <li class="address">
      <svg viewBox="0 0 10 10"><circle cx="5" cy="4" r="2"/><path d="M5 9.5 C2 6 1.5 5 1.5 4 a3.5 3.5 0 0 1 7 0 c0 1 -.5 2 -3.5 5.5z"/></svg>
      Street Name, City Name, Zipcode-012345
    </li>
    <li class="phone">
      <svg viewBox="0 0 10 10"><circle cx="5" cy="5" r="4.3"/><path d="M3.5 3 l1 1 -.5 .7 c.4 .8 .9 1.3 1.6 1.6 l.7-.5 1 1"/></svg>
      012-345-6789
    </li>
    <li class="email">
      <svg viewBox="0 0 10 10"><rect x="1" y="2.5" width="8" height="5.5"/><path d="M1 2.5 l4 3 4-3"/></svg>
      info@brightfieldventures.example
    </li>
    <li class="web">
      <svg viewBox="0 0 10 10"><circle cx="5" cy="5" r="4"/><path d="M1 5h8M5 1c-2 2.5-2 5.5 0 8M5 1c2 2.5 2 5.5 0 8"/></svg>
      www.brightfieldventures.example
    </li>
  </ul>

  <section class="letter">
    <p class="salutation">Dear Mr. Lorem,</p>
    <p class="body-copy">Lorem ipsum dolor sit amet, consectetuer adipiscing elit, sed diam nonummy nibh euismod tincidunt ut laoreet dolore magna aliquam erat volutpat. Ut wisi enim ad minim veniam, quis nostrud exerci tation ullamcorper suscipit lobortis nisl ut aliquip ex ea commodo consequat. Duis autem vel eum iriure dolor in hendiusto odio dignissim qui blandit praesent luptatum zzril delenit augue duis dolore te feugait nulla facilisi.</p>
    <p class="body-copy">Lorem ipsum dolor sit amet, consectetuer adipiscing elit, sed diam nonummy nibh euismod tincidunt ut laoreet dolore magna aliquam erat volutpat. Ut wisi enim ad minim veniam, quis nostrud exerci tation ullamcorper suscipit lobortis nisl ut aliquip ex ea commodo consequat. Duis autem vel eum iriure dolor in hendiusto odio dignissim qui blandit praesent luptatum zzril delenit augue duis dolore te feugait nulla facilisi.</p>
    <p class="body-copy">Lorem ipsum dolor sit amet, consectetuer adipiscing elit, sed diam nonummy nibh euismod tincidunt ut laoreet dolore magna aliquam erat volutpat. Ut wisi enim ad minim veniam, quis nostrud exerci tation ullamcorper suscipit lobortis nisl ut aliquip ex ea commodo consequat. Duis autem vel eum iriure dolor in hendiusto odio dignissim qui blandit praesent luptatum zzril delenit augue duis dolore te feugait nulla facilisi.</p>
    <p class="closing">Sincerely Your,</p>
    <p class="signature">Your Name</p>
  </section>

  <div class="footer-band"></div>
</main>
</body>
</html>
```